Exciting new aperitif brand needs a great label

Vel-Orin is a wonderful rich new premium-priced bitter aperitif, with a deep red colour, from a 100+ year old distillery (1890) near Turin in the Piedmont region of Italy. Inspired by Tessoni, it is perfectly formulated to elevate the classic Bravetti cocktail (and variations on it). It also goes perfectly in a Spritz or a long mixed drink with soda or tonic. The name Vel-Orin is derived from the French for 'peak' and the Italian word for 'love'.

The label, which should take inspiration from Tessoni, but be distinctively different, can incoporate any number of premium label embellishments (foil, embossing, textures etc) and should be no greater than 11cm (height) x 9cm (width) with any core imagery restricted to a width of c.7cm.

The attached mood board should act as inspiration and colour should largely be restricted to reds, blues, whites and perhaps orange. For completeness, the label should note that the ABV is 25% and the bottle size 70cl.

Target Market(s)

21-45yr olds - equal split female/male

Colors
0054AA
0677BA
7BADD7
CADEEF
E8F1F8
0094D4
00A9DD
6FCCEA
C7EBF8
E9F6FB
EE7325
F08F49
F5BC92
FAE3D3
FDF4ED
EB3D1F
EC4F4E
F09395
F8D3D4
FCEDEE

Requirements
Must have
• Great lettering design on the name Vel-Orin

```html
<!DOCTYPE html>
<html lang="en">
<head>
<meta charset="utf-8">
<title>Vel-Orin Bitter Aperitivo Label</title>
<link rel="stylesheet" href="https://fonts.googleapis.com/css2?family=Sancreek&family=Roboto+Slab:wght@400&family=Berkshire+Swash&family=Alfa+Slab+One&display=swap">
<style>
  :root {
    --navy-deep: #02041f;
    --navy: #0a1550;
    --blue-mid: #0b2a8a;
    --mountain-blue: #06296a;
    --sun-red: #ff0000;
    --snow: #f4f6fa;
    --gold-light: #f7e08a;
    --gold: #d9a73a;
    --gold-dark: #b2742a;
    --white: #ffffff;
  }
  html, body {
    margin: 0;
    padding: 0;
    overflow: hidden;
    background: #ffffff;
  }
  .label {
    position: relative;
    width: 982px;
    height: 1200px;
    overflow: hidden;
    background: linear-gradient(135deg, var(--gold-dark) 0%, var(--gold) 25%, var(--gold-dark) 50%, var(--gold-light) 80%, var(--gold) 100%);
  }
  .label__panel {
    position: absolute;
    left: 14px;
    top: 14px;
    width: 954px;
    height: 1173px;
    background: var(--navy-deep);
    overflow: hidden;
  }
  .label__artwork {
    position: absolute;
    left: 0;
    top: 316px;
    width: 954px;
    height: 857px;
    background:
      radial-gradient(circle at 50% 38%, var(--sun-red) 0%, #d40000 30%, rgba(180,0,0,0) 46%),
      linear-gradient(180deg, var(--navy-deep) 0%, var(--blue-mid) 35%, var(--mountain-blue) 70%, var(--mountain-blue) 100%);
  }
  .label__type {
    position: absolute;
    left: 0;
    top: 0;
    width: 954px;
    height: 1173px;
  }
  .brand-name {
    font-family: "Sancreek", serif;
    font-size: 300px;
  }
  .tagline {
    font-family: "Roboto Slab", serif;
    font-size: 23px;
  }
  .origin {
    font-family: "Berkshire Swash", cursive;
    font-size: 54px;
  }
  .strength {
    font-family: "Alfa Slab One", serif;
    font-size: 56px;
  }
</style>
</head>
<body>
  <main class="label">
    <div class="label__panel">
      <div class="label__artwork" role="img" aria-label="Illustration of a red sun rising behind snow-capped blue mountain peaks, with a white heart above the central summit"></div>
      <svg class="label__type" viewBox="0 0 954 1173" xmlns="http://www.w3.org/2000/svg">
        <defs>
          <linearGradient id="silver" x1="0" y1="0" x2="0" y2="1">
            <stop offset="0" stop-color="#e4e4e4"/>
            <stop offset="0.3" stop-color="#ffffff"/>
            <stop offset="0.55" stop-color="#c9c9c9"/>
            <stop offset="1" stop-color="#f2f2f2"/>
          </linearGradient>
          <linearGradient id="gold-foil" x1="0" y1="0" x2="1" y2="0">
            <stop offset="0" stop-color="#f7d565"/>
            <stop offset="0.5" stop-color="#c98a1e"/>
            <stop offset="1" stop-color="#f5dc6a"/>
          </linearGradient>
        </defs>
        <text class="brand-name" x="477" y="263" text-anchor="middle" textLength="822" lengthAdjust="spacingAndGlyphs" fill="url(#silver)" stroke="#0a0f3a" stroke-width="4" paint-order="stroke">VEL-ORIN</text>
        <text class="tagline" x="477" y="302" text-anchor="middle" textLength="697" lengthAdjust="spacing" fill="var(--gold-light)">BITTER APERITIVO</text>
        <text class="origin" x="477" y="1024" text-anchor="middle" textLength="330" lengthAdjust="spacingAndGlyphs" fill="url(#gold-foil)">Made In Italy</text>
        <text class="strength" x="482" y="1120" text-anchor="middle" textLength="361" lengthAdjust="spacing" fill="var(--white)">25% ABV</text>
      </svg>
    </div>
  </main>
</body>
</html>
```